New Fun, Positive, energised looking Business Card Needed for High Achiever Coach

I am looking for a two sided full colour business card. I am self employed and have recently re branded my 1-2-1 work re-vitalising high achievers. My target client base for these cards is therefore high achievers - usually aged 40 -55, they are often entrepreneurs, CEO or work in banking and finance and 2/3 are male. I work with them on 90 day or 6 month coaching programs to help them live their success in a healthier, more sustainable and fulfiiled way. They pay for this privately so though they are corporate types the cards need not look 'corporate'. I want to portray the idea of transformation, vitality and re-connecting.
You can get a feel for the look I like on my new website: morvenlisk.co.uk
I want to use this logo with strapline (Re-Vitalising High Achievers) (I purchased off Logoharbor) and font/ colours (the turquoise and green).
Details to include on the card:
www.morvenlisk.co.uk
+44 7915 302618
morven@morvenlisk.co.uk
skype: morvenlisk
I'd also like to include:
Do you struggle to switch off? Want to be healthier and feel fitter? Want closer relationships? More clarity over the direction you are headed? I can help you do these things using integrated mind-body techniques. Visit morvenlisk.co.uk TODAY to apply for a FREE Breakthrough session.
BUT if that is too much text for a card I am open to advice/ammendments.
Updates
Thanks for your design - I am considering them. PLease change the wording to :

```html
<!DOCTYPE html>
<html lang="en">
<head>
<meta charset="utf-8">
<title>Morven Lisk – Business Card</title>
<link href="https://fonts.googleapis.com/css2?family=Open+Sans:wght@400;600;700&display=swap" rel="stylesheet">
<style>
  :root {
    --turquoise: #13a6cc;
    --green: #67bd6a;
    --white: #ffffff;
    --ink: #3a3f44;
    --divider: #d5d8db;
    --backdrop: #eceae6;
  }
  * { box-sizing: border-box; margin: 0; padding: 0; }
  html, body {
    width: 1200px; height: 720px; overflow: hidden;
    background: var(--backdrop);
    font-family: "Open Sans", Arial, sans-serif;
  }
  .sheet {
    width: 1200px; height: 720px;
    display: flex; align-items: center; justify-content: center; gap: 40px;
  }
  .card {
    position: relative;
    width: 540px; height: 309px;
    overflow: hidden;
    box-shadow: 0 6px 18px rgba(0,0,0,.18);
  }

  /* Front */
  .card--front { background: var(--white); }
  .brand {
    position: absolute; left: 40px; top: 112px; width: 210px;
    display: flex; align-items: center; gap: 10px;
  }
  .brand__dot {
    width: 18px; height: 18px; border-radius: 50%;
    background: var(--turquoise); flex: none;
  }
  .brand__name {
    font-weight: 700; font-size: 30px; line-height: 1;
    color: var(--turquoise); white-space: nowrap;
  }
  .divider {
    position: absolute; left: 270px; top: 40px;
    width: 1px; height: 150px; background: var(--divider);
  }
  .contacts {
    position: absolute; left: 290px; top: 52px;
    list-style: none; font-size: 14.5px; color: var(--ink);
  }
  .contacts li { display: flex; align-items: center; gap: 8px; height: 24px; }
  .contacts svg { width: 13px; height: 13px; flex: none; }
  .front-band { position: absolute; left: 0; bottom: 0; width: 540px; height: 70px; }

  /* Back */
  .card--back { display: flex; flex-direction: column; color: var(--white); text-align: center; }
  .back__questions {
    flex: 0 0 150px; background: var(--green);
    display: flex; align-items: flex-end; justify-content: center;
    padding-bottom: 14px; font-size: 15.5px; line-height: 1.4;
  }
  .back__offer {
    flex: 1; background: var(--turquoise);
    display: flex; flex-direction: column; align-items: center; justify-content: flex-start;
    padding-top: 16px; font-size: 15.5px; line-height: 1.4;
  }
  .back__offer p + p { margin-top: 8px; }
  .back__offer strong { font-weight: 700; }
</style>
</head>
<body>
<main class="sheet">

  <section class="card card--front" aria-label="Card front">
    <div class="brand">
      <span class="brand__dot"></span>
      <span class="brand__name">Morven Lisk</span>
    </div>
    <div class="divider"></div>
    <ul class="contacts">
      <li>
        <svg viewBox="0 0 16 16"><circle cx="8" cy="8" r="8" fill="var(--turquoise)"/><path d="M5.2 4.2l1.5-.3.8 2-1 .8a6 6 0 0 0 2.8 2.8l.8-1 2 .8-.3 1.5c-3.6.3-6.9-3-6.6-6.6z" fill="#fff"/></svg>
        +44 7915 302618
      </li>
      <li>
        <svg viewBox="0 0 16 16"><circle cx="8" cy="8" r="8" fill="var(--turquoise)"/><rect x="4" y="5.2" width="8" height="5.6" fill="#fff"/><path d="M4 5.2l4 3 4-3" stroke="var(--turquoise)" fill="none" stroke-width="1"/></svg>
        morven@morvenlisk.co.uk
      </li>
      <li>
        <svg viewBox="0 0 16 16"><circle cx="8" cy="8" r="8" fill="var(--turquoise)"/><circle cx="8" cy="8" r="4.2" fill="none" stroke="#fff" stroke-width="1"/><ellipse cx="8" cy="8" rx="1.8" ry="4.2" fill="none" stroke="#fff" stroke-width="1"/><path d="M3.8 8h8.4" stroke="#fff" stroke-width="1"/></svg>
        www.morvenlisk.co.uk
      </li>
      <li>
        <svg viewBox="0 0 16 16"><circle cx="8" cy="8" r="8" fill="var(--turquoise)"/></svg>
        morvenlisk
      </li>
    </ul>
    <svg class="front-band" viewBox="0 0 540 70" preserveAspectRatio="none" aria-hidden="true">
      <polygon points="0,52 380,52 400,40 540,40 540,70 0,70" fill="var(--turquoise)"/>
      <polygon points="392,52 420,30 540,8 540,40 410,40" fill="var(--green)"/>
    </svg>
  </section>

  <section class="card card--back" aria-label="Card back">
    <div class="back__questions">
      <p>Do you struggle to switch off?<br>
      Want to be healthier and feel fitter?<br>
      Want closer relationships?<br>
      More clarity over the direction you are headed?</p>
    </div>
    <div class="back__offer">
      <p>I can help you do these things using integrated<br>mind-body techniques.</p>
      <p>Visit <strong>morvenlisk.co.uk</strong> TODAY to apply for a<br>FREE Breakthrough session.</p>
    </div>
  </section>

</main>
</body>
</html>
```